July 2022 Industrial Manufacturer Product Expo Mexico City

We manufacture large screws and fastners for large Mining equipment, Trains, large ships, airplanes, wind turbines, and so on. We also do custom work base on the customer needs. No matter the size we can make it.
We have a Expo coming up with companies all over the world. We have to stand out we are a family own business so our customer service will be above and beyond anyone can provide. We do not have a sales force to push our products and services we provide one on one service.
Plus@!! I'm looking for anything that you designers can come up with if it was your company to put on a business card, plus i want to do a 1 or 2 sided pamphlet, and then a website. We make Speciality Bolts for large mining equipment these bolts can be 3 to 4 foot long!!! Plus fasteners, Nuts, washers, any, size, strengths, special materials, we offer more of a ono on one customer service, We are a small company, family own, but can fulfill any type of orders. We can also provide special time lines for emergency orders. "We keep the machines running we here at KRV don't believe in down time" We want to hear any slogan based on our company to stand out.
Thanks i really appreciate all your work and options that we have to pick on. Plus just a thought we could possibly want to entertain a experience Marketing internet help maybe a employment possibility. Thanks

I need 2 cards one in Spanish and English Like the steel back ground maybe send me in some bright red and blue writing Same with the Black cards Please remove the word Military The logo KRV maybe integrate a picture of a Bolt 🔩 Thank you

Still looking for I need 2 cards one in Spanish and English Like the steel back ground maybe send me in some bright red and blue writing Same with the Black cards try bright writing Please remove the word Military The logo KRV maybe integrate a picture of a Bolt 🔩 Plus will need the company to make a brochure and website next Thank you

Target Market(s)

Large Mining, Ship, Train, Green Energy, VELM, and Government equipment. Throughout the World

Industry/Entity Type

We can Custom Manufacture any type of Fastners for Mining equipment, Trains, Ships, Green energy, Governments, or military projects. wind turbines,

Contact Information for Business Card

I attached the name and contact info that's on a card, plus the Company Logo. Would like industrial looking background with Bright Colors that will stand out!! If we can insert somewhere maybe on back that we "Custom Manufacture Any Size or Quantity Fastners for Large Mining Equipment, Trains, Ships, Green Energy Equipment or Government Projects

Font styles to use
Other font styles liked:
• You Pick, has to be bold, colorful standout, Professional looking Beable to read it.

Colors

Designer to choose colors to be used in the design.

Requirements
Must have
• Need in Spanish and English TO STANDOUT FROM THE REST OF THE EXPO!! See Business card details, Rounded corners
Nice to have
• Can i see some of the darker cards with Bright Red and Blue letters I like to see the different type of card material, heavy thickness, plastic, transparent, Metal types, Bright Colors, I saw like Raised letters like on the logo.

```html
<!DOCTYPE html>
<html lang="es">
<head>
<meta charset="utf-8">
<title>KRV — Tarjeta de presentación / Business card</title>
<link rel="stylesheet" href="https://fonts.googleapis.com/css2?family=Ubuntu:ital,wght@0,400;0,500;0,700;1,500&display=swap">
<style>
  :root {
    --stage: #2b2b2e;
    --card-white: #ffffff;
    --blue-bright: #0a86d8;
    --blue-mid: #0a5fb8;
    --navy: #0b1f8a;
    --graphite: #3c3c40;
    --graphite-dark: #1e1e21;
    --steel: #6a6a70;
    --text-dark: #1a1f5c;
    --band-text: #ffffff;
    --band-text-soft: #d6e8fa;
  }
  * { box-sizing: border-box; margin: 0; padding: 0; }
  html, body {
    width: 1200px; height: 866px; overflow: hidden;
    background: var(--stage);
    font-family: "Ubuntu", "Segoe UI", sans-serif;
  }
  .stage {
    width: 1200px; height: 866px;
    display: flex; flex-direction: column;
    align-items: center; justify-content: center; gap: 50px;
  }
  .card {
    position: relative;
    width: 620px; height: 354px;
    border-radius: 6px;
    overflow: hidden;
    box-shadow: 0 14px 30px rgba(0,0,0,.55);
  }

  /* ---------- Front ---------- */
  .card--front { background: var(--card-white); }
  .card--front .name {
    position: absolute; left: 40px; top: 44px;
    font-size: 27px; font-weight: 500; font-style: italic;
    color: var(--blue-bright); letter-spacing: .3px;
  }
  .card--front .rule { position: absolute; height: 1px; background: var(--navy); }
  .rule--top { left: 30px; top: 84px; width: 560px; }
  .rule--phones { left: 360px; top: 232px; width: 230px; }
  .card--front .contact {
    position: absolute; left: 40px; top: 100px;
    font-size: 17px; line-height: 1.3; color: var(--text-dark);
  }
  .brand-mark {
    position: absolute; display: flex; align-items: center; gap: 12px;
    font-family: "Ubuntu", sans-serif; font-weight: 700;
  }
  .card--front .brand-mark { right: 70px; top: 118px; font-size: 64px; color: var(--blue-mid); }
  .brand-mark .dot { width: 16px; height: 16px; border-radius: 50%; background: currentColor; }
  .phones {
    position: absolute; right: 34px; top: 242px;
    font-size: 18px; line-height: 1.25; color: var(--text-dark);
    text-align: right; letter-spacing: 1.5px;
  }
  .phones li { list-style: none; display: flex; align-items: center; justify-content: flex-end; gap: 8px; }
  .phones svg { width: 16px; height: 16px; }
  .front-base { position: absolute; left: 0; bottom: 0; width: 620px; height: 120px; }

  /* ---------- Back ---------- */
  .card--back {
    background: linear-gradient(155deg, var(--graphite-dark) 0%, var(--graphite) 45%, var(--steel) 100%);
  }
  .card--back .texture {
    position: absolute; inset: 0;
    background: linear-gradient(115deg, rgba(0,0,0,.35) 0%, rgba(0,0,0,0) 40%, rgba(255,255,255,.06) 70%, rgba(0,0,0,.2) 100%);
  }
  .card--back .brand-mark { right: 60px; top: 34px; font-size: 80px; color: #d9dadd; }
  .claim-band {
    position: absolute; left: 0; top: 152px; width: 100%; height: 160px;
    background: linear-gradient(90deg, var(--blue-bright) 0%, var(--blue-mid) 55%, var(--navy) 100%);
    display: flex; flex-direction: column; align-items: center; justify-content: center; gap: 10px;
    padding: 0 28px;
  }
  .claim {
    text-transform: uppercase; text-align: center;
    font-size: 13.5px; line-height: 1.35; letter-spacing: .4px;
  }
  .claim--en { color: var(--band-text); }
  .claim--es { color: var(--band-text-soft); }
  .card--back .edge {
    position: absolute; left: 0; bottom: 0; width: 100%; height: 18px;
    background: linear-gradient(180deg, rgba(0,0,0,0), rgba(0,0,0,.45));
  }
</style>
</head>
<body>
<main class="stage">

  <article class="card card--front" aria-label="Tarjeta, frente / Card front">
    <h1 class="name">Lic. Marisol Ventura Ocampo</h1>
    <div class="rule rule--top"></div>
    <p class="contact">Cotizaciones / Quotes<br>ventas@krvtornillos.mx</p>
    <div class="brand-mark"><span>KRV</span><span class="dot"></span></div>
    <div class="rule rule--phones"></div>
    <ul class="phones">
      <li>5550142876
        <svg viewBox="0 0 16 16" aria-hidden="true"><path d="M3 2l3 0 1 4-2 1c1 2 2 3 4 4l1-2 4 1 0 3c-6 1-12-5-11-11z" fill="var(--blue-mid)"/></svg>
      </li>
      <li>5550193341
        <svg viewBox="0 0 16 16" aria-hidden="true"><rect x="4" y="1.5" width="8" height="13" rx="1.5" fill="none" stroke="var(--blue-mid)" stroke-width="1.6"/><circle cx="8" cy="12" r="1" fill="var(--blue-mid)"/></svg>
      </li>
    </ul>
    <svg class="front-base" viewBox="0 0 620 120" aria-hidden="true">
      <defs>
        <linearGradient id="baseGrey" x1="0" y1="0" x2="0" y2="1">
          <stop offset="0" stop-color="#8a8a8e"/>
          <stop offset="1" stop-color="#2e2e31"/>
        </linearGradient>
        <linearGradient id="baseBlue" x1="0" y1="0" x2="1" y2="0">
          <stop offset="0" stop-color="#0a86d8"/>
          <stop offset="1" stop-color="#0b1f8a"/>
        </linearGradient>
      </defs>
      <path d="M0 14 L250 70 C290 78 320 64 360 74 C420 88 520 102 620 110 L620 120 L0 120 Z" fill="url(#baseGrey)"/>
      <path d="M0 10 L250 66 L250 72 L0 16 Z" fill="url(#baseBlue)"/>
    </svg>
  </article>

  <article class="card card--back" aria-label="Tarjeta, reverso / Card back">
    <div class="texture" role="img" aria-label="Fondo de acero oscuro facetado"></div>
    <div class="brand-mark"><span>KRV</span><span class="dot"></span></div>
    <div class="claim-band">
      <p class="claim claim--en" lang="en">Custom manufacture any size or quantity fasteners for large<br>mining equipment, trains, ships, green energy equipment<br>or government projects</p>
      <p class="claim claim--es">Fabricamos tornillería a medida de cualquier tamaño o cantidad<br>para equipo minero, trenes, barcos, equipo de energía verde<br>o proyectos de gobierno</p>
    </div>
    <div class="edge"></div>
  </article>

</main>
</body>
</html>
```